sydney wedding photography business needs a business card design

we need a business card design for a sydney based wedding photography and videography business. our business name is :golden hour studio and film. our target clients are 24-35 yrs female. our style is candid, organic, natural, dynamic. we are a team of young photographers and videographers, and help brides to create memories that they will cherish for the rest of their lives. the logo will be provided. we want an elegant design that reflects our style, and also want to give a great impression to our clients that we are one of the best studios in sydney and our brand means quality and premium service.

Target Market(s)

bride to be, 24-35 years old, living in sydney and surrunding areas

Industry/Entity Type

Wedding Photography

Contact Information for Business Card

address: 57 tarrant street, glenmore nsw 2047
mobile: 0431872259
phone: (02) 9163 2408
info@tidewillowstudio.net.au
www.tidewillowstudio.net.au
facebook:tidewillowweddings
instagram:tidewillowweddings

Font styles to use
Serif
Sans Serif

Requirements
Nice to have
• maybe add my slogan"Stories Worth Keeping" if the layout looks good
Should not have
• no black color, not good idea for wedding biz card

```html
<!DOCTYPE html>
<html lang="en">
<head>
<meta charset="utf-8">
<title>Golden Hour Studio and Film – Business Card</title>
<link rel="stylesheet" href="https://fonts.googleapis.com/css2?family=Josefin+Sans:wght@400;600&display=swap">
<style>
  :root {
    --backdrop: #e8e5e0;
    --card: #ffffff;
    --gold: #b8862b;
    --bronze: #7a4a18;
    --ink: #2e2822;
    --rule: #4a423a;
  }
  * { box-sizing: border-box; margin: 0; padding: 0; }
  html, body { width: 1200px; height: 900px; overflow: hidden; }
  body {
    background: var(--backdrop);
    font-family: "Josefin Sans", sans-serif;
    color: var(--ink);
    position: relative;
  }
  .card {
    position: absolute;
    top: 301px;
    width: 515px;
    height: 297px;
    background: var(--card);
    box-shadow: 0 2px 8px rgba(0,0,0,0.12);
  }
  .card--front { left: 72px; }
  .card--back { left: 614px; }

  /* Front */
  .brand-frame {
    position: absolute;
    left: 101px; top: 106px;
    width: 312px; height: 83px;
    border: 1.5px solid var(--gold);
    display: flex; flex-direction: column;
    align-items: center; justify-content: center;
    color: var(--gold);
    font-weight: 600;
  }
  .brand-name { font-size: 34px; line-height: 1; letter-spacing: 0.5px; white-space: nowrap; }
  .brand-sub { font-size: 12px; letter-spacing: 6px; margin-top: 8px; white-space: nowrap; }
  .slogan {
    position: absolute;
    left: 101px; top: 205px; width: 312px;
    text-align: center;
    font-size: 12px; letter-spacing: 5.6px;
    white-space: nowrap;
  }
  .slogan-lead { color: var(--bronze); }
  .slogan-tail { color: var(--gold); }

  /* Back */
  .info-frame {
    position: absolute;
    left: 34px; top: 28px;
    width: 446px; height: 240px;
    border: 1px solid var(--rule);
    display: grid;
    grid-template-columns: 224px 1fr;
    grid-template-rows: 105px 107px 1fr;
  }
  .info-brand {
    grid-column: 1 / 3;
    border-bottom: 1px solid var(--rule);
    display: flex; flex-direction: column;
    align-items: center; justify-content: center;
    color: var(--gold); font-weight: 600;
  }
  .info-brand .brand-name { font-size: 32px; }
  .info-brand .brand-sub { font-size: 11px; margin-top: 8px; }
  .contact-list {
    border-right: 1px solid var(--rule);
    border-bottom: 1px solid var(--rule);
    list-style: none;
    padding: 18px 0 0 30px;
    font-size: 12.5px;
    line-height: 18px;
    white-space: nowrap;
  }
  .contact-list li, .place-list li { display: flex; align-items: center; gap: 7px; }
  .icon { width: 11px; height: 11px; flex: none; fill: var(--gold); }
  .detail-col {
    border-bottom: 1px solid var(--rule);
    display: grid; grid-template-rows: 38px 1fr;
    min-width: 0;
  }
  .services {
    border-bottom: 1px solid var(--rule);
    display: flex; align-items: center; justify-content: center;
    font-size: 11.5px;
    white-space: nowrap;
  }
  .place-list {
    list-style: none;
    padding: 10px 0 0 31px;
    font-size: 12.5px; line-height: 18px;
    white-space: nowrap;
  }
  .place-list .indent { padding-left: 18px; }
  .social-row {
    grid-column: 1 / 3;
    display: flex; align-items: center; justify-content: center;
    gap: 8px;
    font-size: 12.5px;
  }
  .social-item { display: flex; align-items: center; gap: 4px; }
  .social-square { width: 10px; height: 10px; background: var(--gold); border-radius: 2px; }
</style>
</head>
<body>
  <section class="card card--front">
    <div class="brand-frame">
      <span class="brand-name">Golden Hour</span>
      <span class="brand-sub">STUDIO AND FILM</span>
    </div>
    <p class="slogan"><span class="slogan-lead">STORIES</span> <span class="slogan-tail">WORTH KEEPING</span></p>
  </section>

  <section class="card card--back">
    <div class="info-frame">
      <header class="info-brand">
        <span class="brand-name">Golden Hour</span>
        <span class="brand-sub">STUDIO AND FILM</span>
      </header>

      <ul class="contact-list">
        <li><svg class="icon" viewBox="0 0 12 12"><circle cx="6" cy="6" r="6"/><circle cx="6" cy="4.6" r="2" fill="#fff"/><path d="M2.6 9.8a3.6 3.2 0 0 1 6.8 0z" fill="#fff"/></svg>DANIEL HART</li>
        <li><svg class="icon" viewBox="0 0 12 12"><rect x="3" y="0.5" width="6" height="11" rx="1"/><rect x="4" y="1.8" width="4" height="7" fill="#fff"/></svg>0431 872 259</li>
        <li><svg class="icon" viewBox="0 0 12 12"><path d="M1 5c0-2 2.5-3 5-3s5 1 5 3l-2 1-1-1.5H4L3 6z"/><rect x="3" y="6.5" width="6" height="4" rx="1"/></svg>(02) 9163 2408</li>
        <li><svg class="icon" viewBox="0 0 12 12"><rect x="0.5" y="2" width="11" height="8" rx="1"/><path d="M1 2.5l5 4 5-4" fill="none" stroke="#fff" stroke-width="1"/></svg>info@tidewillowstudio.net.au</li>
      </ul>

      <div class="detail-col">
        <p class="services">WEDDING | ENGAGEMENT | FAMILY</p>
        <ul class="place-list">
          <li><svg class="icon" viewBox="0 0 12 12"><path d="M6 0.5a4 4 0 0 1 4 4c0 3-4 7-4 7s-4-4-4-7a4 4 0 0 1 4-4z"/><circle cx="6" cy="4.5" r="1.5" fill="#fff"/></svg>57 tarrant street</li>
          <li class="indent">glenmore nsw 2047</li>
          <li><svg class="icon" viewBox="0 0 12 12"><circle cx="6" cy="6" r="5.3" fill="none" stroke="#b8862b" stroke-width="1.2"/><ellipse cx="6" cy="6" rx="2.2" ry="5.3" fill="none" stroke="#b8862b" stroke-width="1"/><path d="M0.7 6h10.6" stroke="#b8862b" stroke-width="1"/></svg>www.tidewillowstudio.net.au</li>
        </ul>
      </div>

      <footer class="social-row">
        <span class="social-item"><span class="social-square"></span>tidewillowweddings</span>
        <span class="social-item"><span class="social-square"></span>tidewillowweddings</span>
      </footer>
    </div>
  </section>
</body>
</html>
```